Toms welding and seed cleaning Business cards

Jakes welding and seed cleaningWe clean wheat seed on farm with portable cleaners so the farmers have pure wheat seed to plant back for the next crop. We are certified to clean foundation, registered, and certified seed wheat. Our cleaners being portable make it easier for the farmers because we do it right on there farm so they don't have to haul it all to townWhen there is no wheat to clean we weld in the winter. We improve, add onto, and build new corrals. We also build sheds, cattle shelters, and wind breaks. Other welding is welcomed

Reason: I need to extend the deadline because I've been busy and not had my game together. I need more time figure out what I want yet

Industry/Entity Type

Agriculture

Contact Information for Business Card

Just "toms welding and seed cleaning" on front and other info on the back
On the back side I would like to have my address.
Morris Tulane
48213 W COUNTY RD 318
BRANWELL KS 67588
Phone #5804419362

Font styles to use
Sans Serif

Requirements
Must have
• list we are certified to clean foundation, registered, and certified wheat
• State that they are portable cleaners
• For the welding part list, add on to, improve on, and repair existing corrals and new corrals and other welding welcomed
Nice to have
• A wheat field with some metal corrals on the side with a nice classic looking barn for a background. Maybe some cattle in the corrals
• A nice looking farm yard would be good too

```html
<!DOCTYPE html>
<html lang="en">
<head>
<meta charset="utf-8">
<title>Welding and seed cleaning – Business card</title>
<link rel="stylesheet" href="https://fonts.googleapis.com/css2?family=Quicksand:wght@300;700&family=Share+Tech&family=Varela+Round&family=Fredoka:wght@600&display=swap">
<style>
  :root{
    --sky:#5f8fc9;
    --field:#8a7a5c;
    --rail:#a4552a;
    --paper:#ffffff;
    --sun:#f6ee6a;
    --sun-soft:#fbf6b8;
    --ribbon:#e9ebe4;
    --heading:#1d7bb5;
    --item:#3b9ad6;
    --bullet:#c9cbc9;
    --ink:#111111;
    --rule:rgba(255,255,255,.55);
  }
  *{margin:0;padding:0;box-sizing:border-box}
  html,body{width:1200px;height:702px;overflow:hidden;background:#fff}
  .card{position:relative;width:1200px;height:702px;overflow:hidden;background:linear-gradient(135deg,var(--sun-soft),var(--sun) 60%)}
  .photo{position:absolute;left:0;top:0;width:600px;height:702px;
    background:
      linear-gradient(180deg,transparent 30%,rgba(164,85,42,.35) 45%,rgba(164,85,42,.25) 70%,transparent 80%),
      linear-gradient(180deg,#3f74c0 0%,#8fb0d6 28%,#9a8d74 45%,#6f6248 70%,#a79a7c 100%);}
  .back-panel{position:absolute;inset:0}
  .rule{position:absolute;left:0;width:600px;height:2px;background:var(--rule)}
  .name{position:absolute;left:112px;top:126px;font-family:"Quicksand",sans-serif;font-size:49px;color:var(--ink);letter-spacing:1px;white-space:nowrap}
  .name .first{font-weight:700}
  .name .last{font-weight:300}
  .name-rule{position:absolute;left:88px;top:188px;width:510px;height:1px;background:linear-gradient(90deg,rgba(255,255,255,.9),rgba(255,255,255,.3))}
  .icon{position:absolute;fill:#fff}
  .contact{position:absolute;left:179px;font-family:"Share Tech",sans-serif;color:#fff;letter-spacing:2px;white-space:nowrap}
  .address{top:298px;font-size:20px;line-height:30px}
  .phone{top:448px;font-size:25px}
  .banner{position:absolute;height:54px}
  .banner svg{position:absolute;left:0;top:0}
  .banner h2{position:absolute;top:8px;font-family:"Fredoka",sans-serif;font-weight:600;font-size:32px;color:var(--heading);letter-spacing:.5px;white-space:nowrap}
  .list{position:absolute;left:626px;list-style:none;font-family:"Varela Round",sans-serif;font-size:23px;line-height:29px;color:var(--item)}
  .list li{position:relative;padding-left:42px}
  .list li::before{content:"";position:absolute;left:0;top:6px;width:16px;height:15px;background:var(--bullet)}
</style>
</head>
<body>
<div class="card">
  <div class="photo" role="img" aria-label="Blurred photo of rust-red steel corral panels in a dry winter field under a blue sky"></div>

  <div class="rule" style="top:254px"></div>
  <div class="rule" style="top:396px"></div>
  <div class="rule" style="top:531px"></div>

  <div class="name"><span class="first">MORRIS</span> <span class="last">TULANE</span></div>
  <div class="name-rule"></div>

  <svg class="icon" style="left:100px;top:302px" width="46" height="42" viewBox="0 0 46 42" aria-hidden="true">
    <path d="M23 2 L45 21 L40 21 L40 40 L28 40 L28 28 L18 28 L18 40 L6 40 L6 21 L1 21 Z"/>
    <rect x="32" y="5" width="5" height="10"/>
  </svg>
  <div class="contact address">48213 W COUNTY RD 318<br>BRANWELL KS 67588</div>

  <svg class="icon" style="left:98px;top:446px" width="50" height="36" viewBox="0 0 50 36" aria-hidden="true">
    <path d="M4 12 C4 2 46 2 46 12 L46 15 L36 15 L36 10 L14 10 L14 15 L4 15 Z"/>
    <path d="M10 34 L14 16 L36 16 L40 34 Z"/>
    <circle cx="25" cy="25" r="6" fill="#7a6a55"/>
    <circle cx="25" cy="25" r="3"/>
  </svg>
  <div class="contact phone">5804419362</div>

  <svg class="back-panel" width="1200" height="702" viewBox="0 0 1200 702" aria-hidden="true">
    <defs>
      <linearGradient id="paperEdge" x1="0" x2="1" y1="0" y2="0">
        <stop offset="0" stop-color="#f3f6e0"/>
        <stop offset=".04" stop-color="#fff"/>
        <stop offset="1" stop-color="#fff"/>
      </linearGradient>
    </defs>
    <polygon points="600,0 1048,0 1181,210 1181,640 1067,682 600,682" fill="url(#paperEdge)"/>
  </svg>

  <div class="banner" style="left:606px;top:36px">
    <svg width="280" height="56" viewBox="0 0 280 56" aria-hidden="true"><polygon points="0,0 260,0 280,28 260,56 0,56" fill="var(--ribbon)"/></svg>
    <h2 style="left:37px">WELDING</h2>
  </div>
  <ul class="list" style="top:123px">
    <li>Add on to</li>
    <li style="margin-top:17px">Improve on</li>
    <li style="margin-top:16px">Repair existing<br>corrals</li>
    <li style="margin-top:18px">New corrals and<br>other welding</li>
  </ul>

  <div class="banner" style="left:606px;top:370px">
    <svg width="280" height="58" viewBox="0 0 280 58" aria-hidden="true"><polygon points="0,0 260,0 280,29 260,58 0,58" fill="var(--ribbon)"/></svg>
    <h2 style="left:17px;top:9px">SEED CLEANING</h2>
  </div>
  <ul class="list" style="top:447px">
    <li>Certified to clean<br>foundation</li>
    <li style="margin-top:25px">Portable cleaners</li>
    <li style="margin-top:27px">Registered and Certified</li>
  </ul>
</div>
</body>
</html>
```